Brightfen Business Card Redesign & Logo Update

We need to update our business cards to something more modern and fresh. Brightfen can provide the current color schemes and old design examples, but welcome creativity in helping us with this redesign. PLEASE NOTE that we no longer utilize the "tree" and/or "leaf" imagery in our branding. If able would apprecaite an update on the quality of our "words only" logo in Ai. / PNG formats too.

Target Market(s)

Investors, landowners, corporate partners, contractors

Industry/Entity Type

Environmental Restoration & Conservation

Contact Information for Business Card

Logo, persons name, title, mailing address, phone and email, website url

Font styles to use
Other font styles liked:
• Merriweather

Requirements
Nice to have
• Logo, persons name, title, mailing address, phone and email, website url, but open to ideams
Should not have
• No all back backgrounds

```html
<!DOCTYPE html>
<html lang="en">
<head>
<meta charset="utf-8">
<title>Brightfen Business Cards</title>
<link href="https://fonts.googleapis.com/css2?family=Open+Sans:wght@400;700&family=Oswald:wght@500&display=swap" rel="stylesheet">
<style>
  :root {
    --bg: #d6d6d6;
    --paper: #f1f0ed;
    --green: #15803d;
    --orange: #ee7d1e;
    --ink: #111111;
    --grey: #7a7a7a;
  }
  * { margin: 0; padding: 0; box-sizing: border-box; }
  html, body { width: 1200px; height: 1051px; overflow: hidden; background: var(--bg); }
  .stage {
    position: relative; width: 1200px; height: 1051px;
    display: flex; align-items: center; justify-content: center; gap: 40px;
  }
  .card {
    position: relative; width: 540px; height: 309px;
    background: var(--paper);
    border-bottom: 4px solid var(--green);
    box-shadow: 0 10px 28px rgba(0,0,0,0.18);
    font-family: "Open Sans", sans-serif;
  }
  .brand { display: flex; flex-direction: column; align-items: flex-start; }
  .brand-name {
    font-family: "Open Sans", sans-serif; font-weight: 700;
    color: var(--green); letter-spacing: 1px; line-height: 1;
  }
  .brand-tagline {
    font-family: "Oswald", sans-serif; font-weight: 500;
    color: var(--ink); text-transform: uppercase; letter-spacing: 0.5px; line-height: 1.2;
  }
  /* front */
  .card-front { display: flex; align-items: center; justify-content: center; }
  .card-front .brand-name { font-size: 62px; }
  .card-front .brand-tagline { font-size: 18px; margin-top: 6px; }
  /* back */
  .card-back { display: flex; align-items: center; padding: 0 26px; }
  .card-back .brand { width: 250px; }
  .card-back .brand-name { font-size: 38px; }
  .card-back .brand-tagline { font-size: 11px; margin-top: 4px; }
  .divider { width: 1px; height: 170px; background: var(--green); margin: 0 22px 0 8px; }
  .contact { color: var(--grey); font-size: 12.5px; line-height: 1.45; }
  .person-name { color: var(--green); font-weight: 700; font-size: 16px; text-transform: uppercase; letter-spacing: 0.5px; }
  .person-title { margin-bottom: 8px; }
  .address { margin-bottom: 8px; }
  .contact-line { display: flex; align-items: center; gap: 7px; }
  .contact-line svg { width: 11px; height: 11px; flex: none; fill: var(--orange); }
</style>
</head>
<body>
<main class="stage">
  <section class="card card-back">
    <div class="brand">
      <span class="brand-name">BRIGHTFEN</span>
      <span class="brand-tagline">Environmental Credit Company</span>
    </div>
    <div class="divider"></div>
    <div class="contact">
      <div class="person-name">Evan Marlow</div>
      <div class="person-title">President</div>
      <div class="address">1842 Cove Ridge Road<br>Seabrook CA 90210</div>
      <div class="contact-line">
        <svg viewBox="0 0 24 24" aria-hidden="true"><path d="M6.6 10.8a15.1 15.1 0 0 0 6.6 6.6l2.2-2.2c.3-.3.7-.4 1-.2 1.1.4 2.3.6 3.6.6.6 0 1 .4 1 1V20c0 .6-.4 1-1 1A17 17 0 0 1 3 4c0-.6.4-1 1-1h3.5c.6 0 1 .4 1 1 0 1.3.2 2.5.6 3.6.1.3 0 .7-.2 1z"/></svg>
        <span>555-014-2290</span>
      </div>
      <div class="contact-line">
        <svg viewBox="0 0 24 24" aria-hidden="true"><path d="M2 5h20v14H2z M2 5l10 8 10-8" fill="var(--orange)"/><path d="M2 5l10 8 10-8" fill="none" stroke="#f1f0ed" stroke-width="2"/></svg>
        <span>emarlow@brightfen.com</span>
      </div>
      <div class="contact-line">
        <svg viewBox="0 0 24 24" aria-hidden="true"><circle cx="12" cy="12" r="10"/><path d="M2 12h20M12 2c3 3 3 17 0 20M12 2c-3 3-3 17 0 20" fill="none" stroke="#f1f0ed" stroke-width="1.5"/></svg>
        <span>www.brightfen.com</span>
      </div>
    </div>
  </section>

  <section class="card card-front">
    <div class="brand">
      <span class="brand-name">BRIGHTFEN</span>
      <span class="brand-tagline">Environmental Credit Company</span>
    </div>
  </section>
</main>
</body>
</html>
```